Build a landing page to promote a service (dialler consultation and support).

We are a call centre consultation firm and we need a landing page to promote a service. The service is Tormalux dialler consultation and support.
If you do not know what Tormalux is, please do some quick "Zorvex" research for more information.
The landing page will be promoted with a paid advertisement, so we want something that is simple, and explains exactly what service we offer.
There are two objectives for the landing page:
1) A "call to action" which directs the user to a contact page, including a form plus all of our contact details.
2) A form for them viewers to enter their details to get a "FREE" quote for their project. This form should be placed on the main page.
Notes:
The call to action will require the viewer to enter their name, email, phone number as well as a description of their request. There will also need to be a drop down menu for the type of quote. This menu should have the following options:
1) Tormalux support
2) Tormalux hosting
3) Tormalux customisation
4) Other
We need 2 pages in total:
1) Main landing page
This is the home page. It will need to clearly indicate our services and our key selling features.
Services:
* Tormalux support
* Tormalux hosting
* Tormalux customisation
Key Selling Features:
* Australian based
* PCI complaint
* 10+ years of dialler and call centre experience
* we run a sister company which is a highly reputable 40 seat call centre, so we know first hand about call centre technology.
The main landing page will have an "about us" section with a few paragraphs about how we got started.
-------------------------------------------------------------------------
2) Contact page
All of our contact details will live on this page, as well as a contact form.
Other notes:
We will be self hosting the landing page.
We already have a domain name.
The design must be clean and incorporate our logo, as well as it's colours. (Logo attached)
We want a fully function HTML landing page, not just a "PSD" design.
The page must be mobile optimised.
Anyone using Tormalux software.

```html
<!DOCTYPE html>
<html lang="en">
<head>
<meta charset="utf-8">
<title>Contact Us – Nexacall Tormalux Support</title>
<link href="https://fonts.googleapis.com/css2?family=Poppins:wght@400;500;600&family=Roboto:wght@500;700&family=Roboto+Condensed:wght@700&display=swap" rel="stylesheet">
<style>
:root{
  --blue:#1a7bc7;
  --teal:#22b09a;
  --ink:#1e1e1e;
  --text:#333;
  --line:#bbb;
  --foot:#f4f4f4;
  --white:#fff;
  --map:#e3e5e0;
}
*{box-sizing:border-box;margin:0;padding:0}
html,body{width:694px;height:1200px;overflow:hidden;background:var(--white)}
body{font-family:"Poppins",sans-serif;color:var(--text);position:relative}
.abs{position:absolute}
.header{left:0;top:0;width:694px;height:54px;background:var(--white);box-shadow:0 1px 3px rgba(0,0,0,.15);z-index:3}
.brand-badge{left:62px;top:0;width:124px;height:80px;background:var(--white);border-radius:0 0 62px 62px;z-index:4;display:flex;flex-direction:column;align-items:center;padding-top:5px}
.brand-dot{width:38px;height:38px;border-radius:50%;background:var(--blue)}
.brand-name{font-family:"Poppins",sans-serif;font-weight:500;font-size:15px;line-height:18px;color:var(--blue);margin-top:2px}
.nav{left:226px;top:20px;display:flex;gap:17px;z-index:4;font-family:"Roboto",sans-serif;font-weight:500;font-size:10.5px;color:#222;letter-spacing:.2px}
.nav-phone{left:438px;top:19px;z-index:4;display:flex;align-items:center;gap:5px;font-family:"Roboto",sans-serif;font-weight:500;font-size:11px;color:var(--blue);letter-spacing:.4px}
.nav-contact{left:543px;top:16px;width:75px;height:21px;border:1.5px solid var(--teal);border-radius:11px;z-index:4;display:flex;align-items:center;justify-content:center;gap:4px;font-size:8.5px;color:var(--teal);font-weight:500}
.hero{left:0;top:54px;width:694px;height:234px;background:linear-gradient(90deg,#25b29a 0%,#26a6a8 45%,#2b8fc4 100%)}
.hero-title{right:78px;top:146px;font-family:"Roboto Condensed",sans-serif;font-weight:700;font-size:35px;color:var(--white);text-shadow:0 2px 3px rgba(0,0,0,.2)}
.map{left:76px;top:326px;width:542px;height:223px;background:var(--map);border:1px solid #d6d9d2}
.map-pin{left:339px;top:424px}
.section-title{font-family:"Roboto",sans-serif;font-weight:700;font-size:17px;color:var(--ink)}
.field{left:76px;width:257px;height:22px;border:1px solid var(--line);font-size:6.5px;font-style:italic;color:#666;padding:7px 9px;background:var(--white)}
.field-select{display:flex;justify-content:space-between;align-items:center;padding:0 9px}
.field-select::after{content:"";border-top:4px solid #666;border-left:3px solid transparent;border-right:3px solid transparent}
.submit{left:76px;top:760px;width:71px;height:18px;background:var(--blue);color:var(--white);font-size:8px;font-weight:600;display:flex;align-items:center;justify-content:center}
.office-intro{left:372px;top:618px;width:215px;font-size:8.4px;line-height:13.5px}
.info{left:370px;display:flex;gap:12px;font-size:7.6px;line-height:11px;align-items:flex-start}
.info svg{flex:none}
.partners{left:0;top:842px;width:694px;height:64px;border-top:1px solid #e3e3e3;border-bottom:1px solid #e3e3e3}
.partner{top:24px;height:18px;background:#9a9a9a;border-radius:2px}
.footer{left:0;top:906px;width:694px;height:294px;background:var(--foot)}
.foot-brand{left:76px;top:12px;display:flex;flex-direction:column;align-items:center}
.follow{right:77px;top:30px;display:flex;align-items:center;gap:3px;font-size:11.5px;color:#222}
.follow span{margin-right:8px}
.social{width:15px;height:15px;border:1px solid #444;border-radius:50%}
.rule{left:76px;width:542px;height:1px;background:#dcdcdc}
.foot-head{font-family:"Roboto",sans-serif;font-weight:500;font-size:13px;color:#222;letter-spacing:.2px}
.foot-head b{color:var(--teal);font-weight:700}
.foot-text{font-size:7.2px;line-height:12px;color:#333}
.email-input{left:76px;top:168px;width:159px;height:23px;border:1px solid #ccc;border-radius:12px;background:var(--white);font-size:7px;padding:6px 9px;color:#333}
.signup{left:244px;top:169px;width:66px;height:21px;background:var(--teal);border-radius:11px;color:var(--white);font-size:9px;font-weight:600;display:flex;align-items:center;justify-content:center}
.links{left:543px;top:132px;list-style:none;font-size:7.4px;line-height:13px}
.links li::before{content:"";display:inline-block;border-left:3px solid #333;border-top:2px solid transparent;border-bottom:2px solid transparent;margin-right:7px;vertical-align:1px}
.copyright{left:0;top:258px;width:694px;text-align:center;font-size:7.2px;color:#333}
</style>
</head>
<body>

<header class="abs header"></header>
<div class="abs brand-badge">
  <div class="brand-dot"></div>
  <div class="brand-name">Nexacall</div>
</div>
<nav class="abs nav"><span>HOME</span><span>ABOUT</span><span>SERVICES</span><span>BLOG</span></nav>
<div class="abs nav-phone">
  <svg width="10" height="12" viewBox="0 0 10 12"><path d="M2 0l2 3-1.3 1.3c.6 1.6 1.6 2.9 3 3.9L7 7l3 2-1 2.5C4.5 11 1 6.5 0 1.5z" fill="var(--blue)"/></svg>
  0800 555 010
</div>
<div class="abs nav-contact">
  <svg width="9" height="7" viewBox="0 0 9 7"><rect width="9" height="7" rx="1" fill="var(--teal)"/><path d="M0 .5l4.5 3.5L9 .5" stroke="#fff" fill="none" stroke-width=".9"/></svg>
  CONTACT
</div>

<section class="abs hero" role="img" aria-label="Smiling call centre agent wearing a headset, tinted teal to blue"></section>
<h1 class="abs hero-title">CONTACT US</h1>

<div class="abs map" role="img" aria-label="Street map of the surrounding area with the head office location marked"></div>
<svg class="abs map-pin" width="16" height="22" viewBox="0 0 9 13" aria-hidden="true"><path d="M4.5 0A4.5 4.5 0 0 0 0 4.5C0 8 4.5 13 4.5 13S9 8 9 4.5A4.5 4.5 0 0 0 4.5 0z" fill="var(--blue)"/><circle cx="4.5" cy="4.5" r="1.7" fill="#fff"/></svg>

<h2 class="abs section-title" style="left:76px;top:580px">Inquiries</h2>
<div class="abs field" style="top:619px">Your first name</div>
<div class="abs field" style="top:643px">Your email</div>
<div class="abs field" style="top:667px">Your Phone</div>
<div class="abs field field-select" style="top:691px"><span>Quote type: Tormalux support / hosting / customisation / Other</span></div>
<div class="abs field" style="top:715px;height:38px">Message</div>
<div class="abs submit">SUBMIT</div>

<h2 class="abs section-title" style="left:367px;top:580px">Head Office</h2>
<p class="abs office-intro">For Tormalux support, hosting or customisation, please be in touch!</p>
<div class="abs info" style="top:655px">
  <svg width="9" height="13" viewBox="0 0 9 13"><path d="M4.5 0A4.5 4.5 0 0 0 0 4.5C0 8 4.5 13 4.5 13S9 8 9 4.5A4.5 4.5 0 0 0 4.5 0z" fill="#222"/><circle cx="4.5" cy="4.5" r="1.7" fill="#fff"/></svg>
  <span style="margin-left:1px">Nexacall<br>48 Harlow Street, Ste 12, Brook-<br>vale, New York 10455</span>
</div>
<div class="abs info" style="top:694px;align-items:center">
  <svg width="9" height="13" viewBox="0 0 9 13"><rect width="9" height="13" rx="1.5" fill="#222"/><rect x="1.5" y="1.8" width="6" height="8" fill="#fff"/></svg>
  <span style="font-size:8.5px">Phone:&nbsp; +1 555-014-2290</span>
</div>
<div class="abs info" style="top:719px;align-items:center">
  <svg width="11" height="8" viewBox="0 0 11 8"><rect width="11" height="8" rx="1" fill="#222"/><path d="M0 .6l5.5 4L11 .6" stroke="#fff" fill="none"/></svg>
  <span>Email:&nbsp; hello@nexacall.com</span>
</div>
<div class="abs info" style="top:740px;align-items:center">
  <svg width="12" height="12" viewBox="0 0 12 12"><rect x="3" y="0" width="7" height="4" fill="#222"/><rect x="0" y="4" width="12" height="8" rx="1" fill="#222"/><rect x="4" y="6" width="6" height="4" fill="#fff"/></svg>
  <span style="font-size:8.5px">Fax: (555) 0199 2231</span>
</div>

<section class="abs partners" aria-label="Partners">
  <div class="abs partner" style="left:78px;width:34px"></div>
  <div class="abs partner" style="left:144px;width:60px"></div>
  <div class="abs partner" style="left:237px;width:58px"></div>
  <div class="abs partner" style="left:326px;width:58px"></div>
  <div class="abs partner" style="left:430px;width:44px"></div>
  <div class="abs partner" style="left:513px;width:62px"></div>
</section>

<footer class="abs footer">
  <div class="abs foot-brand">
    <div class="brand-dot"></div>
    <div class="brand-name" style="font-size:15px">Nexacall</div>
  </div>
  <div class="abs follow"><span>Follow us</span><i class="social"></i><i class="social"></i><i class="social"></i><i class="social"></i></div>
  <div class="abs rule" style="top:78px"></div>

  <h3 class="abs foot-head" style="left:78px;top:103px">SIGN UP FOR <b>NEWSLETTER</b></h3>
  <p class="abs foot-text" style="left:78px;top:136px;width:250px">Excepteur sint occaecat cupidatat non proident, sunt in culpa qui officia deserunt Excepteur sint occaecat cupidatat non proident</p>
  <div class="abs email-input">Enter email</div>
  <div class="abs signup">SIGN UP</div>

  <h3 class="abs foot-head" style="left:357px;top:104px">CONTACT <b>US</b></h3>
  <div class="abs foot-text" style="left:357px;top:136px;display:flex;gap:11px">
    <svg width="8" height="10" viewBox="0 0 9 13"><path d="M4.5 0A4.5 4.5 0 0 0 0 4.5C0 8 4.5 13 4.5 13S9 8 9 4.5A4.5 4.5 0 0 0 4.5 0z" fill="var(--teal)"/><circle cx="4.5" cy="4.5" r="1.7" fill="#fff"/></svg>
    <span>Nexacall<br>48 Harlow Street, Ste 12<br>Brookvale, New York 10455</span>
  </div>
  <div class="abs foot-text" style="left:357px;top:177px;display:flex;gap:11px;align-items:center">
    <svg width="8" height="8" viewBox="0 0 10 12"><path d="M2 0l2 3-1.3 1.3c.6 1.6 1.6 2.9 3 3.9L7 7l3 2-1 2.5C4.5 11 1 6.5 0 1.5z" fill="var(--teal)"/></svg>
    <span>Phone: +1 555-014-2290</span>
  </div>
  <div class="abs foot-text" style="left:357px;top:193px;display:flex;gap:11px;align-items:center">
    <svg width="8" height="6" viewBox="0 0 11 8"><rect width="11" height="8" rx="1" fill="var(--teal)"/><path d="M0 .6l5.5 4L11 .6" stroke="#fff" fill="none"/></svg>
    <span>Email: support@nexacall.com</span>
  </div>

  <h3 class="abs foot-head" style="left:541px;top:104px;font-size:12px">QUICK <b>LINKS</b></h3>
  <ul class="abs links">
    <li>Home</li><li>About us</li><li>Our Services</li><li>Blog</li><li>FAQ</li><li>Contact Us</li>
  </ul>

  <div class="abs rule" style="top:235px"></div>
  <p class="abs copyright">© Copyright 2018 Nexacall. All Rights Reserved.&nbsp; Privacy Policy &nbsp;|&nbsp; Disclaimer &nbsp;|&nbsp; Terms &amp; Conditions</p>
</footer>

</body>
</html>
```